design a construction company business card

Design business card around our logo. Card must have all the typical info: name, title, address, phone, email, business name, etc. Somewhere on the card I would like to see our motto "Built on integrity... Inspired by commitment." Consider adding a splash of bright orange to the card to complement the blues and silvers/grays in the logo. We are open to metallic inks, textures, etc. We would like to see options on both light and dark backgrounds. The font in the logo is Euro Technic Extended Regular.

```html
<!DOCTYPE html>
<html lang="en">
<head>
<meta charset="utf-8">
<title>Halvern Building – Business Card</title>
<link rel="stylesheet" href="https://fonts.googleapis.com/css2?family=Roboto:ital,wght@0,300;0,400;0,500;1,400&display=swap">
<style>
  :root {
    --page-bg: #e9e6e1;
    --card-white: #ffffff;
    --brand-blue: #2563ad;
    --brand-navy: #2a3a94;
    --accent-orange: #f29a1f;
    --text-gray: #4a4a4a;
    --rule-gray: #6f6f6f;
  }
  * { margin: 0; padding: 0; box-sizing: border-box; }
  html, body {
    width: 1200px;
    height: 1198px;
    overflow: hidden;
    background: var(--page-bg);
    font-family: "Roboto", Arial, sans-serif;
  }
  .card {
    position: absolute;
    left: 270px;
    width: 626px;
    height: 390px;
    box-shadow: 0 14px 28px rgba(0,0,0,0.22);
  }
  .card--front { top: 190px; background: var(--card-white); }
  .card--back {
    top: 614px;
    background: linear-gradient(180deg, var(--brand-blue) 0%, var(--brand-navy) 100%);
  }

  /* Front */
  .brand-name {
    position: absolute;
    left: 0; right: 0;
    top: 92px;
    text-align: center;
    color: var(--brand-blue);
    font-weight: 500;
    letter-spacing: 3px;
    line-height: 1.15;
  }
  .brand-name__main { display: block; font-size: 54px; }
  .brand-name__sub { display: block; font-size: 19px; letter-spacing: 4px; }

  .accent-bar {
    position: absolute;
    left: 0; top: 262px;
    width: 9px; height: 75px;
    background: var(--accent-orange);
  }
  .name-plate {
    position: absolute;
    left: 20px; top: 262px;
    width: 247px; height: 75px;
    background: linear-gradient(180deg, var(--brand-blue), var(--brand-navy));
    color: #fff;
    padding: 13px 0 0 45px;
  }
  .name-plate__name { font-size: 27px; font-weight: 300; line-height: 1.05; letter-spacing: 0.5px; }
  .name-plate__title { font-size: 14px; font-weight: 400; line-height: 1.3; }

  .contact-rule {
    position: absolute;
    left: 334px; top: 252px;
    width: 1px; height: 96px;
    background: var(--rule-gray);
  }
  .contact-list {
    position: absolute;
    left: 355px; top: 253px;
    list-style: none;
    color: var(--text-gray);
    font-size: 14px;
    line-height: 16px;
  }
  .contact-list li { display: flex; align-items: flex-start; margin-bottom: 9px; }
  .contact-list svg { width: 22px; height: 22px; flex: none; margin-right: 9px; fill: var(--brand-blue); }
  .contact-list .phone { margin-top: 2px; }
  .contact-list .email { margin-top: 6px; }

  /* Back */
  .motto {
    position: absolute;
    left: 76px; top: 92px;
    color: #fff;
    font-style: italic;
    font-weight: 400;
    font-size: 34px;
    line-height: 57px;
  }
</style>
</head>
<body>

<section class="card card--front" aria-label="Card front">
  <h1 class="brand-name">
    <span class="brand-name__main">HALVERN</span>
    <span class="brand-name__sub">BUILDING, INC.</span>
  </h1>

  <div class="accent-bar"></div>
  <div class="name-plate">
    <p class="name-plate__name">MARCUS DALE</p>
    <p class="name-plate__title">General Manager</p>
  </div>

  <div class="contact-rule"></div>
  <ul class="contact-list">
    <li class="address">
      <svg viewBox="0 0 24 24" aria-hidden="true"><path d="M12 1a8 8 0 0 0-8 8c0 5.5 8 14 8 14s8-8.5 8-14a8 8 0 0 0-8-8zm0 11a3.2 3.2 0 1 1 0-6.4A3.2 3.2 0 0 1 12 12z"/></svg>
      <span>4812 Ridgefield Ave. Houston<br>TX 77041</span>
    </li>
    <li class="phone">
      <svg viewBox="0 0 24 24" aria-hidden="true"><path d="M6.6 10.8a15 15 0 0 0 6.6 6.6l2.2-2.2a1 1 0 0 1 1-.25 11.4 11.4 0 0 0 3.6.57 1 1 0 0 1 1 1V20a1 1 0 0 1-1 1A17 17 0 0 1 3 4a1 1 0 0 1 1-1h3.5a1 1 0 0 1 1 1c0 1.25.2 2.45.57 3.57a1 1 0 0 1-.25 1z"/></svg>
      <span>281-555-0147</span>
    </li>
    <li class="email">
      <svg viewBox="0 0 24 24" aria-hidden="true"><path d="M2 5h20v14H2zm2 2v.3l8 5.6 8-5.6V7zm0 2.7V17h16V9.7l-8 5.6z"/></svg>
      <span>mdale@halvernbuilding.com</span>
    </li>
  </ul>
</section>

<section class="card card--back" aria-label="Card back">
  <p class="motto">“Built on<br>integrity...<br>Inspired by<br>commitment.”</p>
</section>

</body>
</html>
```